Therapy Dog Business need a brochure

I need a brochure designed for my Canine Assisted Therapy business in Victoria Australia. I have a logo already and info and photos to upload.
Best as white background and using the colours from the logo please
Updates

Hi Everyone,
I am sorry to have to revise the brief. I have added three new photos I was unable to add due to the size. I have had to wait for my photographer to change the size to add them today. I have been really inspired by all the work you have done so far. Thank you.
Could you please add the following on the brochure. (Under the individual dogs photo)
1. Pepper is the white dog. Please add the following under her picture. Pepper is one of the first Court Dogs in Australia. Working in Victoria, she has worked in the following Courts. The Halbrook Inquest Court, The Brindle Hearing Court in Collingwood, and the Fenwick Court in Melbourne CBD. Her ability to use her intuition for clients is inspiring. Please contact us for potential use in Courts. Pepper has worked at the Marlow Constabulary College, and at TALON at Mar Con. She is a stunning dog!
2. Barnaby is the golden dog. Barnaby is Peppers son, and had her instinct of intuition of who needs his help. Barnaby has an incredible soft approach as does his mother Pepper. He is incredibly safe with young children, and yet has a playful nature for adolescents and adults alike. He is soft and caring, and like his mother will go to those who need him most. Barnaby like his mother has worked at Marlow Constabulary, his time at MC included the Marlow Constabulary Directorate (MCD) Both he and his mother have very impressive CV'S!
3. Tansy the black dog. Tansy is my Therapy and Assistance dog "trainer" she is safe and stable with all the dogs and people I train for Therapy Dog Training and Assistance Dog Training. She has also been with me on my journey as a Counsellor and I have been able to work alongside her and Pepper for Counselling sessions.
She is soft, caring, and also intuitive. I am incredibly grateful for her help, as well as Pepper and Barnaby.
ALSO I am so sorry to add this but could you also add the following: Maybe in dot point?
Court Dog Availability
Therapy Dog Visits - Lawyers - Courts - Child Protection
Police Station / Ambulance Station / Fire Station - Visits
Private Therapy Dog Sessions
website and email confirmation coming soon. Thank you

Target Market(s)

First Responders

Requirements
Must have
• All the photos provided.
Should not have
• Generic photos

```html
<!DOCTYPE html>
<html lang="en">
<head>
<meta charset="utf-8">
<title>Canine Assisted Therapy Brochure – Inside Spread</title>
<link rel="stylesheet" href="https://fonts.googleapis.com/css2?family=Montserrat:wght@400;600;700;800&display=swap">
<style>
  :root {
    --stage: #d6d6d6;
    --paper: #ffffff;
    --panel: #f7f6f3;
    --frame: #e6e2da;
    --frame-line: #cfc8bb;
    --heading: #4a1822;
    --body-text: #3a3434;
    --rule: #a99e8c;
    --leaf: #b3261e;
    --photo-light: #e9dcc0;
    --photo-light-bg: #8fb0d8;
    --photo-dark: #2a2422;
    --photo-dark-bg: #a4684a;
  }
  * { box-sizing: border-box; margin: 0; padding: 0; }
  html, body {
    width: 1200px; height: 1000px; overflow: hidden;
    background: var(--stage);
    font-family: "Montserrat", Arial, sans-serif;
    color: var(--body-text);
  }
  .brochure {
    position: absolute; left: 60px; top: 140px;
    width: 1080px; height: 720px;
    background: var(--paper);
    display: grid; grid-template-columns: 360px 720px;
    box-shadow: 0 18px 40px rgba(0,0,0,.22);
  }
  .panel { position: relative; padding: 18px; }
  .panel + .panel { border-left: 1px solid #e4e4e4; }
  .panel-frame {
    height: 100%;
    background: var(--panel);
    border: 12px solid var(--frame);
    outline: 1px solid var(--frame-line);
    outline-offset: -12px;
  }
  /* Intro panel */
  .intro .panel-frame { padding: 26px 26px 24px; display: flex; flex-direction: column; }
  .photo-stack { position: relative; height: 250px; margin-bottom: 18px; }
  .photo {
    position: absolute; border: 6px solid #fff;
    box-shadow: 0 4px 10px rgba(0,0,0,.25);
  }
  .photo-golden {
    left: 110px; top: 0; width: 150px; height: 140px;
    background: radial-gradient(ellipse at 50% 60%, var(--photo-light) 0 38%, var(--photo-light-bg) 62%);
    transform: rotate(4deg);
  }
  .photo-black {
    left: 6px; top: 92px; width: 150px; height: 145px;
    background: radial-gradient(ellipse at 45% 62%, var(--photo-dark) 0 36%, var(--photo-dark-bg) 60%);
    transform: rotate(-3deg);
  }
  .leaf-mark {
    position: absolute; left: 200px; top: 168px; width: 30px; height: 30px;
    background: var(--leaf); border-radius: 4px; transform: rotate(8deg);
  }
  .intro h2 {
    font-size: 21px; font-weight: 800; line-height: 1.1;
    color: var(--heading); margin-bottom: 12px;
  }
  .intro p { font-size: 14.5px; line-height: 1.75; }
  /* Spread panel */
  .spread .panel-frame { padding: 30px 38px 30px; }
  .spread h2 {
    font-size: 27px; font-weight: 800; color: var(--heading);
    padding-bottom: 8px; border-bottom: 2px solid var(--rule);
    margin-bottom: 14px;
  }
  .points { list-style: none; }
  .points li {
    position: relative; padding-left: 16px;
    font-size: 13.5px; line-height: 1.6; margin-bottom: 8px;
  }
  .points li::before {
    content: ""; position: absolute; left: 2px; top: 9px;
    width: 5px; height: 5px; border-radius: 50%; background: var(--heading);
  }
  .points strong { color: var(--heading); font-weight: 700; }
  .why-box {
    margin-top: 20px; padding: 20px 24px 12px;
    background: #fff;
    border: 2px solid var(--frame);
    outline: 1px solid var(--frame-line); outline-offset: 3px;
  }
  .why-box h2 { border-bottom: none; padding-bottom: 0; margin-bottom: 12px; }
</style>
</head>
<body>
  <main class="brochure">
    <section class="panel intro">
      <div class="panel-frame">
        <div class="photo-stack">
          <div class="photo photo-golden" role="img" aria-label="Photo of a cream Labrador therapy dog against a blue background"></div>
          <div class="photo photo-black" role="img" aria-label="Photo of a black Labrador therapy dog in front of a brick wall"></div>
          <div class="leaf-mark" role="img" aria-label="Small red maple leaf ornament"></div>
        </div>
        <h2>What is Canine Assisted Therapy?</h2>
        <p>Canine Assisted Therapy (CAT) is a unique form of therapy that integrates trained therapy dogs into the healing process. By working alongside licensed therapists, these compassionate and well-trained dogs help support individuals in overcoming emotional, physical, and psychological challenges. This innovative approach promotes healing, reduces stress, and enhances overall well-being.</p>
      </div>
    </section>

    <section class="panel spread">
      <div class="panel-frame">
        <h2>Benefits of Canine Assisted Therapy</h2>
        <ul class="points">
          <li><strong>Emotional Support and Comfort.</strong> Therapy dogs provide immediate emotional support, offering comfort and companionship during therapy sessions. Their calming presence helps reduce feelings of anxiety, stress, and depression, and grief, creating a safe and nurturing environment for healing.</li>
          <li><strong>Stress Relief and Relaxation.</strong> Interacting with dogs has been proven to reduce cortisol (stress hormone) levels and increase serotonin and oxytocin, the "feel-good" hormones. This natural relief from stress makes Canine Assisted Therapy an ideal option for individuals dealing with anxiety, trauma, PTSD, and grief.</li>
          <li><strong>Improved Mental Health.</strong> Therapy dogs encourage social interaction, communication, and emotional expression, helping individuals address mental health challenges such as depression, anxiety, PTSD, and grief. The unconditional love and companionship of a dog can foster trust and openness during therapy sessions.</li>
        </ul>

        <div class="why-box">
          <h2>Why Choose Canine Assisted Therapy?</h2>
          <ul class="points">
            <li><strong>Proven Effectiveness:</strong> Studies and testimonials highlight the positive effects therapy dogs have on emotional, psychological and physical health.</li>
            <li><strong>Non-Invasive and Gentle:</strong> Therapy dogs provide a natural and non-threatening way to engage with patients, making it accessible for individuals who may feel apprehensive about traditional therapy methods.</li>
            <li><strong>Safe and Trustworthy:</strong> All therapy dogs are carefully trained to work with professionals, ensuring that interactions are safe, beneficial, and appropriate for all individuals.</li>
          </ul>
        </div>
      </div>
    </section>
  </main>
</body>
</html>
```